Quill Harbor (IT/Network Services)

Quill Harbor, LLC provides technology services to small and medium businesses. Essentially, anytime you've every thought your business might need an "IT guy" to handle something you could instead call us to handle it. Basically, you can outsource your IT needs to us.

This is a brand new company and so we'll need a brand new website. I'd like to use WordPress to handle the site since that will make things easier for me to maintain in the long run.

The site should include a, more-or-less, static front page with the dynamic data occurring on pages linked from a navigational area.

I have a logo already designed that I would like to see used in the design. The one with "white" in the title is the official logo, just added some other versions for your perusal.

Color queues from the logo but feel free to add other colors where applicable.

The site should feel somewhat corporate but with a "younger" slant (something a 25-35 year old would enjoy).

Pages (either to be added initially or by me after design completion):
"About" section - includes company history, business philosophy, etc.
"Services" section - service options, service approach, service specifics
"Testimonials" section - (eventually)
"News" section - (eventually) industry news, company news, events, blog
Contact Links

Websites to view:
The two largest local competitors:
http://www.brightmarsh-tech.example/
http://www.kelvarworks.example/
Other local competitors:
http://www.tpbllc.example/
http://www.morrowfield.example/

Other info you might find useful:
Domain: qhllc.example
Address:
417 Elm Row S
Suite 512B
Nashville, TN 37288
Phone: 615-555-0187
Emails available for use/display:
info@qhllc.example
sales@qhllc.example

Target Market(s)

Our target clients are mainly small businesses (25 or less computer users) which means we're looking at a lot of start-ups or younger companies. We'll be interacting with many entrepreneurs and young business owners.

Requirements
Must have
• Need full WP theme (not a mockup)

```html
<!DOCTYPE html>
<html lang="en">
<head>
<meta charset="utf-8">
<title>Quill Harbor — IT &amp; Network Services</title>
<link rel="stylesheet" href="https://fonts.googleapis.com/css2?family=Open+Sans:wght@400;600;700&family=Arimo:ital,wght@0,400;0,700;1,400&display=swap">
<style>
:root{
  --orange:#f39c12;
  --orange-dark:#d9860a;
  --ink:#555555;
  --ink-soft:#666666;
  --ink-muted:#8a8a8a;
  --paper:#f3f0ec;
  --paper-light:#faf9f7;
  --white:#ffffff;
  --nav:#4a4a4a;
  --nav-dark:#333333;
  --rule:#e2ddd7;
}
*{box-sizing:border-box;margin:0;padding:0}
html,body{width:960px;height:1200px;overflow:hidden}
body{font-family:"Arimo",Arial,sans-serif;color:var(--ink);background:var(--white);position:relative}
a{color:inherit;text-decoration:none}
.abs{position:absolute}

/* header */
.site-header{position:absolute;left:0;top:0;width:960px;height:123px;background:var(--paper);border-bottom:2px dotted var(--rule)}
.brand{position:absolute;left:112px;top:56px;display:flex;align-items:center;gap:8px}
.brand-mark{width:22px;height:22px;border-radius:50%;background:var(--orange)}
.brand-name{font-family:"Open Sans",sans-serif;font-weight:600;font-size:21px;letter-spacing:1px;color:#6b6b6b}
.utility{position:absolute;right:104px;top:10px;font-size:11px;color:#666}
.utility span{margin:0 5px}
.main-nav{position:absolute;right:104px;top:58px;display:flex;gap:11px}
.main-nav a{height:28px;padding:0 12px;line-height:28px;font-family:"Open Sans",sans-serif;font-weight:600;font-size:12px;color:#fff;background:linear-gradient(var(--nav),var(--nav-dark));border:1px solid #222;box-shadow:0 1px 2px rgba(0,0,0,.25)}
.main-nav a.current{background:linear-gradient(#fbb03b,var(--orange-dark));border-color:#c47a08}

/* hero */
.hero{position:absolute;left:0;top:125px;width:960px;height:354px;background:var(--paper-light);border-bottom:2px dotted var(--rule)}
.hero-frame{position:absolute;left:114px;top:25px;width:432px;height:297px;border:6px solid var(--orange);box-shadow:0 6px 10px rgba(0,0,0,.25);background:linear-gradient(120deg,#1b5e9c,#3aa6e0 45%,#0f3f70)}
.hero-title{position:absolute;left:582px;top:20px;width:290px;font-family:"Open Sans",sans-serif;font-weight:600;font-size:30px;line-height:34px;color:#555}
.hero-text{position:absolute;left:582px;top:95px;width:280px;font-style:italic;font-size:14.5px;line-height:22.5px;color:#666}
.dots{position:absolute;left:676px;top:308px;display:flex;gap:6px}
.dots i{width:15px;height:15px;border-radius:50%;background:radial-gradient(circle at 40% 35%,#ddd,#999)}
.dots i.on{background:radial-gradient(circle at 40% 35%,#ffc24d,var(--orange-dark))}

.btn-more{position:absolute;display:flex;align-items:center;gap:10px;height:32px;padding:0 10px;background:linear-gradient(#fff,#eee);border:1px solid #ddd;box-shadow:0 1px 3px rgba(0,0,0,.2);font-family:"Open Sans",sans-serif;font-weight:600;font-size:12px;color:#444}
.btn-more svg{width:18px;height:18px}

/* welcome */
.welcome{position:absolute;left:0;top:481px;width:960px;height:276px;background:radial-gradient(ellipse at 35% 40%,#fff 40%,#f3f1ee 100%)}
.welcome h1{position:absolute;left:104px;top:41px;font-family:"Open Sans",sans-serif;font-weight:600;font-size:20px;color:#666}
.welcome h1 .name{color:var(--orange)}
.lead{position:absolute;left:104px;top:78px;width:470px;font-style:italic;font-size:11.5px;line-height:16px;color:var(--orange)}
.body-copy{position:absolute;left:104px;top:118px;width:480px;font-style:italic;font-size:11.5px;line-height:16px;color:#666}

.contact-box{position:absolute;left:616px;top:42px;width:240px;height:178px;border:1px solid var(--orange);background:#f7f5f2}
.contact-head{height:32px;background:linear-gradient(#fbb03b,var(--orange));display:flex;align-items:center;justify-content:space-between;padding:0 10px 0 13px;font-family:"Open Sans",sans-serif;font-weight:600;font-size:14px;color:#4a3a1f}
.contact-body{position:relative;height:113px;padding:14px 13px 0;font-style:italic;font-size:10.5px;line-height:16px;color:#444;border-bottom:1px solid #ddd}
.contact-body svg{float:left;margin:0 8px 0 0}
.contact-body em{color:var(--orange)}
.newsletter{height:31px;display:flex;align-items:center;justify-content:space-between;padding:0 10px 0 13px;font-family:"Open Sans",sans-serif;font-weight:600;font-size:13px;color:#444}

/* columns */
.columns{position:absolute;left:0;top:757px;width:960px;height:328px;background:var(--paper);border-top:1px solid #e6e2dc;border-bottom:2px dotted var(--rule)}
.col-title{position:absolute;top:18px;font-family:"Open Sans",sans-serif;font-weight:600;font-size:19px;color:#666}
.news-item{position:absolute;left:104px;width:240px}
.news-item .txt{position:absolute;left:64px;top:0;width:180px;font-style:italic;font-size:11.3px;line-height:16px;color:#555}
.news-item .txt b{font-weight:400;color:var(--orange)}
.news-item .read{position:absolute;left:180px;top:72px;font-style:italic;font-size:10px;color:#333}
.services{position:absolute;left:372px;top:60px;width:230px;list-style:none}
.services li{position:relative;padding-left:22px;margin-bottom:8px;font-style:italic;font-size:11.3px;line-height:16px;color:#666}
.services li::before{content:"";position:absolute;left:0;top:4px;width:8px;height:8px;border-radius:50%;background:var(--orange)}
.testimonial{position:absolute;left:626px;width:232px}
.portrait{position:absolute;left:0;top:0;width:66px;height:60px;border:3px solid #fff;box-shadow:0 1px 3px rgba(0,0,0,.3)}
.testimonial .quote{position:absolute;left:78px;top:0;width:156px;font-style:italic;font-size:11.3px;line-height:16px;color:#666}
.testimonial .meta{position:absolute;left:1px;top:76px;width:230px;display:flex;justify-content:space-between;font-style:italic;font-size:10px;color:#888}
.testimonial .meta b{font-weight:400;font-size:12px;color:var(--orange)}

/* footer */
.site-footer{position:absolute;left:0;top:1087px;width:960px;height:113px;background:#fff}
.foot-links{position:absolute;left:104px;top:23px;font-style:italic;font-size:10px;color:#666}
.foot-links span{margin:0 5px}
.copyright{position:absolute;left:104px;top:51px;font-style:italic;font-size:10px;line-height:16px;color:#666}
.copyright .name{color:var(--orange)}
.follow{position:absolute;left:746px;top:25px;font-style:italic;font-weight:700;font-size:12px;color:#444}
.social{position:absolute;left:746px;top:49px;display:flex;gap:5px}
.social i{width:24px;height:24px;border-radius:3px}
</style>
</head>
<body>

<header class="site-header">
  <a class="brand" href="#"><span class="brand-mark"></span><span class="brand-name">QUILL HARBOR</span></a>
  <nav class="utility"><a href="#">Client Login</a><span>|</span><a href="#">Register</a><span>|</span><a href="#">Site Map</a></nav>
  <nav class="main-nav">
    <a class="current" href="#">HOME</a><a href="#">ABOUT US</a><a href="#">SERVICES</a><a href="#">OUR CLIENTS</a><a href="#">SOLUTIONS</a><a href="#">MAIL US</a>
  </nav>
</header>

<section class="hero">
  <div class="hero-frame" role="img" aria-label="Businessman touching a glowing blue digital interface"></div>
  <h2 class="hero-title">Lorem ipsum dolor sit amet</h2>
  <p class="hero-text">Aliquam molestie, mi et imperdiet euismod, duipurus auctor tellus, et interdum lacus lectuset ante. Sed accumsan sollicitudin sapien, sit amet adipiscing turpis gravida ac.</p>
  <a class="btn-more" href="#" style="left:582px;top:249px">MORE <svg viewBox="0 0 18 18"><circle cx="9" cy="9" r="8" fill="#fff" stroke="#ccc"/><path d="M7.5 5.5 11 9l-3.5 3.5" fill="none" stroke="#999" stroke-width="1.5"/></svg></a>
  <div class="dots"><i class="on"></i><i></i><i></i><i></i></div>
</section>

<section class="welcome">
  <h1>Welcome to&nbsp; <span class="name">QUILL HARBOR</span></h1>
  <p class="lead">Lorem ipsum dolor sit amet, consectetur adipiscing elit. Fusce accumsan, elit a suscipit sagittis, tortor sapien cursus risus, non rhoncus lectus nunc ac nulla.</p>
  <p class="body-copy">Aliquam molestie, mi et imperdiet euismod, dui purus auctor tellus, et interdum lacus lectus et ante. Sed accumsan sollicitudin sapien, sit amet adipiscing turpis gravida ac. In congue, neque ac lobortis volutpat, libero mauris varius mi, vitae suscipit ipsum ligula vitae risus.</p>
  <a class="btn-more" href="#" style="left:104px;top:205px">MORE <svg viewBox="0 0 18 18"><circle cx="9" cy="9" r="8" fill="#fff" stroke="#ccc"/><path d="M7.5 5.5 11 9l-3.5 3.5" fill="none" stroke="#999" stroke-width="1.5"/></svg></a>

  <aside class="contact-box">
    <div class="contact-head">CONTACT US <svg width="18" height="18" viewBox="0 0 18 18"><circle cx="9" cy="9" r="9" fill="#111"/><path d="M5.5 7.5 9 11l3.5-3.5" fill="none" stroke="#fff" stroke-width="1.8"/></svg></div>
    <div class="contact-body">
      <svg width="56" height="46" viewBox="0 0 56 46" aria-hidden="true"><path d="M6 14c0-8 10-12 22-12s22 4 22 12l-8 3-3-6c-7-2-15-2-22 0l-3 6z" fill="#1e6fd0"/><path d="M14 18h28l8 24H6z" fill="#1e6fd0"/><circle cx="28" cy="30" r="8" fill="#fff"/><circle cx="28" cy="30" r="3" fill="#1e6fd0"/></svg>
      Have a question about one our products or services? Fill out our <em>online contact form</em> and we'll be in touch within one business day..
    </div>
    <div class="newsletter">NEWSLETTER SIGN UP <svg width="18" height="18" viewBox="0 0 18 18"><circle cx="9" cy="9" r="8" fill="#fff" stroke="#ccc"/><path d="M7.5 5.5 11 9l-3.5 3.5" fill="none" stroke="#999" stroke-width="1.5"/></svg></div>
  </aside>
</section>

<section class="columns">
  <h3 class="col-title" style="left:104px">Latest News</h3>
  <h3 class="col-title" style="left:372px">Our Services</h3>
  <h3 class="col-title" style="left:626px">Testimonials</h3>

  <article class="news-item" style="top:60px">
    <svg class="abs" style="left:0;top:0" width="50" height="52" viewBox="0 0 50 52" aria-hidden="true"><rect x="2" y="6" width="46" height="44" rx="6" fill="#fff" stroke="#f39c12" stroke-width="3"/><rect x="2" y="6" width="46" height="10" rx="4" fill="#f39c12"/><rect x="10" y="1" width="4" height="10" fill="#f39c12"/><rect x="36" y="1" width="4" height="10" fill="#f39c12"/><text x="25" y="36" text-anchor="middle" font-family="Arimo,Arial,sans-serif" font-size="19" font-weight="700" fill="#444">23</text><text x="25" y="47" text-anchor="middle" font-family="Arimo,Arial,sans-serif" font-size="10" font-weight="700" fill="#444">MAY</text></svg>
    <p class="txt"><b>Lorem ipsum dolor sit amet,</b> consectetur adipiscing elit. Fusce accumsan, elit a suscipit sagittis...</p>
    <a class="read" href="#">Read More</a>
  </article>
  <article class="news-item" style="top:163px">
    <svg class="abs" style="left:0;top:0" width="50" height="52" viewBox="0 0 50 52" aria-hidden="true"><rect x="2" y="6" width="46" height="44" rx="6" fill="#fff" stroke="#f39c12" stroke-width="3"/><rect x="2" y="6" width="46" height="10" rx="4" fill="#f39c12"/><rect x="10" y="1" width="4" height="10" fill="#f39c12"/><rect x="36" y="1" width="4" height="10" fill="#f39c12"/><text x="25" y="36" text-anchor="middle" font-family="Arimo,Arial,sans-serif" font-size="19" font-weight="700" fill="#444">20</text><text x="25" y="47" text-anchor="middle" font-family="Arimo,Arial,sans-serif" font-size="10" font-weight="700" fill="#444">MAY</text></svg>
    <p class="txt"><b>Lorem ipsum dolor sit amet,</b> consectetur adipiscing elit. Fusce accumsan, elit a suscipit sagittis...</p>
    <a class="read" href="#">Read More</a>
  </article>

  <ul class="services">
    <li>Duis aute irure dolor in reprehenderit.</li>
    <li>Sed ut perspiciatis unde omnis iste natus.</li>
    <li>Veritatis et quasi architecto beatae.</li>
    <li>Sit aspernatur aut odit aut fugit, sed quia consequuntur.</li>
    <li>Server Virtualization</li>
    <li>Lorem ipsum dolor sit amet.</li>
    <li>Duis aute irure dolor in.</li>
  </ul>

  <article class="testimonial" style="top:56px">
    <div class="portrait" role="img" aria-label="Portrait of a smiling client" style="background:linear-gradient(135deg,#c9a68a,#6e8fa8)"></div>
    <p class="quote">Lorem ipsum dolor sit amet, consectetur adipiscing elit. Fusce accumsan, elit a suscipit.....</p>
    <div class="meta"><span>Posted on May22, 2012</span><b>By Harlow</b></div>
  </article>
  <article class="testimonial" style="top:167px">
    <div class="portrait" role="img" aria-label="Portrait of a smiling client" style="background:linear-gradient(135deg,#3a3a3a,#d8b8a0)"></div>
    <p class="quote">Lorem ipsum dolor sit amet, consectetur adipiscing elit. Fusce accumsan, elit a suscipit.....</p>
    <div class="meta"><span>Posted on May22, 2012</span><b>By Marisol</b></div>
  </article>

  <a class="btn-more" href="#" style="left:104px;top:265px">MORE <svg viewBox="0 0 18 18"><circle cx="9" cy="9" r="8" fill="#fff" stroke="#ccc"/><path d="M7.5 5.5 11 9l-3.5 3.5" fill="none" stroke="#999" stroke-width="1.5"/></svg></a>
  <a class="btn-more" href="#" style="left:371px;top:270px">MORE <svg viewBox="0 0 18 18"><circle cx="9" cy="9" r="8" fill="#fff" stroke="#ccc"/><path d="M7.5 5.5 11 9l-3.5 3.5" fill="none" stroke="#999" stroke-width="1.5"/></svg></a>
  <a class="btn-more" href="#" style="left:617px;top:270px">MORE <svg viewBox="0 0 18 18"><circle cx="9" cy="9" r="8" fill="#fff" stroke="#ccc"/><path d="M7.5 5.5 11 9l-3.5 3.5" fill="none" stroke="#999" stroke-width="1.5"/></svg></a>
</section>

<footer class="site-footer">
  <nav class="foot-links"><a href="#">Home</a><span>|</span><a href="#">About Us</a><span>|</span><a href="#">Services</a><span>|</span><a href="#">Our Clients</a><span>|</span><a href="#">Solutions</a><span>|</span><a href="#">Mail Us</a></nav>
  <p class="copyright">Copyright © 2012By <span class="name">QUILL HARBOR</span>.<br>All Right Reserved &nbsp;|&nbsp; Privacy Policy</p>
  <p class="follow">Follow Us on:</p>
  <div class="social">
    <i style="background:#3b5a9a"></i><i style="background:#45b0e3"></i><i style="background:#333"></i><i style="background:#f28a1f"></i>
  </div>
</footer>

</body>
</html>
```